Landing page design for my current website

I need a landing page designed for my Wordpress website. My website is Velmorquay.com, and I need a page that will serve as a landing page for online ads I run. Please follow the color scheme of the current website

This web page will be targeted towards real estate owners who are looking for a property manager. Above the fold needs to have a CTA form headlined with "As a Rental Property Owner, I Want More Protection, Less Stress, and Drama-Free Living"

A few highlights that can be listed beyond the CTA and fold

- Comprehensive Property Management
Full-service management covering tenant placement, leasing, maintenance, and inspections.

Maximized Rental Income
Proven strategies to optimize rental rates and minimize vacancies, ensuring higher ROI.

Stress-Free Management
We handle all tenant interactions, maintenance requests, and property issues, so you don't have to.

Experienced Team
Over a decade of experience in managing single-family homes, small multifamily units, and apartment complexes.

Advanced Technology
Utilize cutting-edge property management software for efficient communication, rent collection, and maintenance tracking.

Tenant Screening and Placement
Thorough background checks and tenant screening processes to ensure reliable and responsible tenants.

Regular Property Inspections
Routine inspections to maintain property condition and address issues before they become costly problems.

Legal Compliance
Expertise in local and federal rental laws to keep your properties compliant and avoid legal hassles.

Transparent Reporting
Detailed monthly reports and financial statements to keep you informed about your property's performance.

Personalized Service
Tailored management plans to meet the unique needs of your properties and investment goals.
Effective Tenant Conflict Resolution
Skilled in handling challenging tenant situations, ensuring conflicts are resolved quickly and professionally to maintain a peaceful living environment and protect your investment.

```html
<!DOCTYPE html>
<html lang="en">
<head>
<meta charset="utf-8">
<title>Velmorquay Realty – Rental Property Management</title>
<link rel="stylesheet" href="https://fonts.googleapis.com/css2?family=Montserrat:wght@600;700&family=Roboto:wght@300;400;500&display=swap">
<style>
:root{
  --brand-blue:#12427a;
  --brand-blue-deep:#0e3766;
  --ink:#222;
  --muted:#666;
  --dark:#2f2f2f;
  --white:#fff;
  --line:#e6e8ec;
}
*{box-sizing:border-box;margin:0;padding:0}
html,body{width:833px;height:1200px;overflow:hidden}
body{position:relative;background:linear-gradient(#fff 40%,#f4f5f7 75%,#fff);font-family:"Roboto",sans-serif;color:var(--ink)}
.top-bar{position:absolute;top:0;left:0;width:833px;height:3px;background:var(--brand-blue)}
.hero-photo{position:absolute;top:60px;left:0;width:833px;height:452px;
  background:
   linear-gradient(#f5f5f5 0%,rgba(245,245,245,0) 18%),
   linear-gradient(90deg,#8a5a44 0%,#a0715a 20%,#5e6d48 45%,#4f6a3a 60%,#9fb3c4 78%,#6f8a56 100%)}
.header{position:absolute;top:0;left:0;width:833px;height:80px}
.brand{position:absolute;left:100px;top:24px;display:flex;align-items:center;gap:8px}
.brand-mark{width:40px;height:40px;border-radius:50%;border:3px solid var(--brand-blue)}
.brand-name{font-family:"Montserrat",sans-serif;font-weight:700;font-size:19px;color:var(--brand-blue);letter-spacing:.5px}
.call{position:absolute;left:522px;top:17px;display:flex;align-items:center;gap:6px;font-weight:500;font-size:11.5px;color:var(--ink)}
.call svg{width:20px;height:20px}
.nav{position:absolute;left:475px;top:50px;display:flex;gap:22px;font-weight:500;font-size:10px}
.nav a{color:var(--ink);text-decoration:none}
.nav a.active{color:var(--brand-blue);border-bottom:1.5px solid var(--brand-blue);padding-bottom:1px}
.search{position:absolute;left:711px;top:47px;width:21px;height:21px;border-radius:50%;background:var(--brand-blue);display:flex;align-items:center;justify-content:center}
.lead-form{position:absolute;left:99px;top:100px;width:295px;height:295px;background:var(--brand-blue)}
.lead-form h1{font-family:"Montserrat",sans-serif;font-weight:600;font-size:15.5px;line-height:18.5px;color:var(--white);text-align:center;margin:28px 14px 0}
.field{position:absolute;background:var(--white);font-size:8px;color:#333;padding:7px 14px}
.submit{position:absolute;left:96px;top:227px;width:102px;height:38px;border-radius:20px;background:var(--dark);border:2px solid var(--white);color:var(--white);font-weight:500;font-size:12px;display:flex;align-items:center;justify-content:center}
.arc{position:absolute;left:0;top:430px;width:833px;height:100px}
.feature{position:absolute;width:154px;height:154px;border-radius:50%;background:var(--white);box-shadow:0 3px 10px rgba(0,0,0,.12);text-align:center;padding:0 12px}
.feature .icon{width:30px;height:30px;margin:12px auto 0;border:2px solid var(--ink);border-radius:6px}
.feature h2{font-weight:500;font-size:8.6px;line-height:12px;text-transform:uppercase;margin-top:13px;color:var(--ink)}
.feature p{font-weight:300;font-size:7.4px;line-height:12.2px;color:var(--muted);margin-top:7px}
.feature .go{position:absolute;left:69px;bottom:8px;width:17px;height:17px}
.feature.highlight{background:var(--brand-blue)}
.feature.highlight h2,.feature.highlight p{color:var(--white)}
.feature.highlight .icon{border-color:var(--white)}
.footer-shape{position:absolute;left:0;top:960px;width:833px;height:240px}
.footer-brand{position:absolute;left:0;top:1028px;width:833px;display:flex;justify-content:center;align-items:center;gap:10px}
.footer-brand .brand-mark{border-color:var(--white);width:44px;height:44px}
.footer-brand .brand-name{color:var(--white);font-size:22px}
.footer-nav{position:absolute;left:0;top:1090px;width:833px;display:flex;justify-content:center;gap:18px;font-weight:500;font-size:11px;color:var(--white)}
.copyright{position:absolute;left:0;top:1121px;width:833px;text-align:center;font-size:9px;color:var(--white)}
.social{position:absolute;left:376px;top:1150px;display:flex;gap:6px}
.social span{width:22px;height:22px;border-radius:50%;background:var(--white)}
</style>
</head>
<body>
<div class="hero-photo" role="img" aria-label="Property manager shaking hands with a couple outside an ivy-covered brick house"></div>
<div class="top-bar"></div>

<header class="header">
  <div class="brand"><span class="brand-mark"></span><span class="brand-name">VELMORQUAY REALTY</span></div>
  <div class="call">
    <svg viewBox="0 0 24 24" fill="none" stroke="#12427a" stroke-width="2"><path d="M5 4h4l2 5-2.5 1.5a11 11 0 005 5L15 13l5 2v4a2 2 0 01-2 2A16 16 0 013 6a2 2 0 012-2"/></svg>
    CALL US : +1 555 014 2290
  </div>
  <nav class="nav"><a class="active">HOME</a><a>ABOUT</a><a>FEATURES</a><a>CONTACT</a></nav>
  <div class="search"><svg width="10" height="10" viewBox="0 0 24 24" fill="none" stroke="#fff" stroke-width="3"><circle cx="10" cy="10" r="6"/><path d="M15 15l6 6"/></svg></div>
</header>

<form class="lead-form">
  <h1>As a Rental Property Owner, I Want More Protection, Less Stress, and Drama-Free Living</h1>
  <div class="field" style="left:21px;top:103px;width:123px;height:24px">Enter Name</div>
  <div class="field" style="left:150px;top:103px;width:124px;height:24px">Enter Email</div>
  <div class="field" style="left:21px;top:133px;width:123px;height:24px">Phone</div>
  <div class="field" style="left:150px;top:133px;width:124px;height:24px">Address</div>
  <div class="field" style="left:21px;top:164px;width:253px;height:47px">Message</div>
  <div class="submit">SUBMIT</div>
</form>

<svg class="arc" viewBox="0 0 833 100" preserveAspectRatio="none"><path d="M0 82 Q416 -10 833 82 L833 100 L0 100Z" fill="#fff"/></svg>

<svg width="0" height="0" style="position:absolute"><defs><symbol id="arrow" viewBox="0 0 20 20"><circle cx="10" cy="10" r="8.5" fill="none" stroke="currentColor" stroke-width="1.5"/><path d="M5.5 10h8M10 6.5l3.5 3.5-3.5 3.5" fill="none" stroke="currentColor" stroke-width="1.5"/></symbol></defs></svg>

<section class="feature" style="left:101px;top:433px"><div class="icon"></div><h2>Comprehensive<br>Property Management</h2><p>Full-service management covering tenant placement, leasing, maintenance, and inspections.</p><svg class="go" style="color:#12427a"><use href="#arrow"/></svg></section>
<section class="feature" style="left:260px;top:433px"><div class="icon"></div><h2>Maximized Rental<br>Income</h2><p>Proven strategies to optimize rental rates and minimize vacancies, ensuring higher ROI.</p><svg class="go" style="color:#12427a"><use href="#arrow"/></svg></section>
<section class="feature" style="left:419px;top:433px"><div class="icon"></div><h2>Stress-Free<br>Management</h2><p>We handle all tenant interactions, maintenance requests, and property issues, so you don't have to.</p><svg class="go" style="color:#12427a"><use href="#arrow"/></svg></section>
<section class="feature" style="left:577px;top:433px"><div class="icon"></div><h2>Experienced Team</h2><p>Over a decade of experience in managing single-family homes, small multifamily units, and apartment complexes.</p><svg class="go" style="color:#12427a"><use href="#arrow"/></svg></section>

<section class="feature" style="left:101px;top:596px"><div class="icon"></div><h2>Advanced Technology</h2><p>Utilize cutting-edge property management software for efficient communication, rent collection, and maintenance tracking.</p><svg class="go" style="color:#12427a"><use href="#arrow"/></svg></section>
<section class="feature highlight" style="left:260px;top:596px"><div class="icon"></div><h2>Tenant Screening<br>and Placement</h2><p>Thorough background checks and tenant screening processes to ensure reliable and responsible tenants.</p><svg class="go" style="color:#fff"><use href="#arrow"/></svg></section>
<section class="feature" style="left:419px;top:596px"><div class="icon"></div><h2>Regular Property<br>Inspections</h2><p>Routine inspections to maintain property condition and address issues before they become costly problems.</p><svg class="go" style="color:#12427a"><use href="#arrow"/></svg></section>
<section class="feature" style="left:577px;top:596px"><div class="icon"></div><h2>Legal Compliance</h2><p>Expertise in local and federal rental laws to keep your properties compliant and avoid legal hassles.</p><svg class="go" style="color:#12427a"><use href="#arrow"/></svg></section>

<section class="feature" style="left:180px;top:760px"><div class="icon"></div><h2>Transparent Reporting</h2><p>Detailed monthly reports and financial statements to keep you informed about your property's performance.</p><svg class="go" style="color:#12427a"><use href="#arrow"/></svg></section>
<section class="feature" style="left:339px;top:760px"><div class="icon"></div><h2>Personalized Service</h2><p>Tailored management plans to meet the unique needs of your properties and investment goals.</p><svg class="go" style="color:#12427a"><use href="#arrow"/></svg></section>
<section class="feature" style="left:497px;top:760px"><div class="icon"></div><h2>Effective Tenant<br>Conflict Resolution</h2><p>Skilled in handling challenging tenant situations, ensuring conflicts are resolved quickly and professionally</p><svg class="go" style="color:#12427a"><use href="#arrow"/></svg></section>

<footer>
  <svg class="footer-shape" viewBox="0 0 833 240" preserveAspectRatio="none">
    <path d="M340 24 Q640 0 833 95 L833 240 L340 240Z" fill="#12427a"/>
    <path d="M0 131 Q416 -70 833 150 L833 240 L0 240Z" fill="#2f2f2f" stroke="#fff" stroke-width="3"/>
  </svg>
  <div class="footer-brand"><span class="brand-mark"></span><span class="brand-name">VELMORQUAY REALTY</span></div>
  <nav class="footer-nav"><span>HOME</span><span>/</span><span>ABOUT</span><span>/</span><span>FEATURES</span><span>/</span><span>CONTACT</span><span>/</span><span>TERMS OF USE</span><span>/</span><span>PRIVACY POLICY</span></nav>
  <p class="copyright">© 2024 Velmorquay Realty. All Rights Reserved &nbsp;|&nbsp; Privacy Policy</p>
  <div class="social"><span></span><span></span><span></span></div>
</footer>
</body>
</html>
```